Business Card Design For A Renovation Contractor Company

We need a business card for a new company based in Singapore, our company name is "RB Tolvane". We are a renovation contractor that builds designs into reality. We build more of F&B restaurants, retail stores and commercial offices. We work very closely with designers. The final design should communicate to our client that we are a company that you can trust, that will plan and complete your project without giving you a headache. I like my client to remember my company as "RB". The beauty of SIMPLE is important.

Industry/Entity Type

Contractor

Requirements
Nice to have
• Black or Red base

```html
<!DOCTYPE html>
<html lang="en">
<head>
<meta charset="utf-8">
<title>RB Tolvane — Business Card</title>
<link href="https://fonts.googleapis.com/css2?family=Jost:wght@400;500;600&display=swap" rel="stylesheet">
<style>
  :root {
    --red: #ec2227;
    --ink: #1d1d1d;
    --grey: #3a3a3a;
    --rule: #9a9a9a;
    --paper: #ffffff;
    --backdrop: #e6e6ea;
  }
  html, body {
    margin: 0;
    padding: 0;
    width: 1200px;
    height: 987px;
    overflow: hidden;
    background: var(--backdrop);
    font-family: "Jost", "Futura", sans-serif;
  }
  .canvas {
    position: relative;
    width: 1200px;
    height: 987px;
  }
  .card {
    position: absolute;
    width: 620px;
    height: 354px;
    border-radius: 26px;
    overflow: hidden;
    box-shadow: 0 10px 28px rgba(0,0,0,0.18);
  }

  /* Back side */
  .card-back {
    left: 540px;
    top: 80px;
    background: var(--red);
    color: var(--paper);
  }
  .back-mark {
    position: absolute;
    left: 0;
    right: 0;
    top: 118px;
    display: flex;
    align-items: center;
    justify-content: center;
    gap: 20px;
  }
  .back-mark .dot {
    width: 46px;
    height: 46px;
    border-radius: 50%;
    background: var(--paper);
  }
  .back-mark .name {
    font-size: 64px;
    font-weight: 500;
    letter-spacing: 1px;
    line-height: 1;
  }
  .back-url {
    position: absolute;
    left: 0;
    right: 0;
    top: 262px;
    text-align: center;
    font-size: 20px;
    letter-spacing: 6px;
  }

  /* Front side */
  .card-front {
    left: 40px;
    top: 520px;
    background: var(--paper);
  }
  .front-wave {
    position: absolute;
    inset: 0;
  }
  .brand {
    position: absolute;
    left: 40px;
    top: 58px;
    width: 260px;
  }
  .brand-row {
    display: flex;
    align-items: center;
    gap: 10px;
  }
  .brand-row .dot {
    width: 26px;
    height: 26px;
    border-radius: 50%;
    background: var(--red);
  }
  .brand-row .name {
    font-size: 40px;
    font-weight: 500;
    color: var(--ink);
    line-height: 1;
  }
  .tagline {
    margin-top: 6px;
    padding-top: 4px;
    border-top: 1px solid var(--ink);
    font-size: 15px;
    color: var(--ink);
    letter-spacing: 0.3px;
  }
  .address {
    position: absolute;
    left: 34px;
    top: 262px;
    color: var(--paper);
    font-size: 16px;
    font-style: normal;
    line-height: 1.35;
  }
  .divider {
    position: absolute;
    left: 330px;
    top: 46px;
    width: 2px;
    height: 150px;
    background: linear-gradient(var(--rule), rgba(154,154,154,0));
  }
  .contact {
    position: absolute;
    left: 350px;
    top: 44px;
  }
  .contact .person {
    font-size: 28px;
    font-weight: 600;
    color: var(--red);
    line-height: 1.05;
  }
  .contact .title {
    font-size: 18px;
    color: var(--grey);
    margin-bottom: 14px;
  }
  .contact ul {
    list-style: none;
    margin: 0;
    padding: 0;
  }
  .contact li {
    display: flex;
    align-items: center;
    gap: 8px;
    font-size: 18px;
    color: var(--grey);
    line-height: 1.35;
  }
  .contact li svg {
    width: 14px;
    height: 14px;
    flex: none;
  }
</style>
</head>
<body>
<main class="canvas">

  <section class="card card-back" aria-label="Card back">
    <div class="back-mark">
      <span class="dot"></span>
      <span class="name">RB Tolvane</span>
    </div>
    <div class="back-url">www.rbtolvane.com</div>
  </section>

  <section class="card card-front" aria-label="Card front">
    <svg class="front-wave" viewBox="0 0 620 354" preserveAspectRatio="none">
      <path d="M0 222 C 150 222, 260 300, 380 330 C 470 352, 560 354, 620 345 L620 354 L0 354 Z" fill="var(--red)"/>
      <path d="M0 210 C 150 210, 260 290, 380 320 C 470 342, 560 344, 620 335" fill="none" stroke="var(--ink)" stroke-width="4"/>
    </svg>

    <div class="brand">
      <div class="brand-row">
        <span class="dot"></span>
        <span class="name">RB Tolvane</span>
      </div>
      <div class="tagline">planned well, built with care</div>
    </div>

    <address class="address">
      Door No. Street Name<br>
      City Name, State, Zip Code
    </address>

    <div class="divider"></div>

    <div class="contact">
      <div class="person">Your Name</div>
      <div class="title">Title</div>
      <ul>
        <li>
          <svg viewBox="0 0 14 14"><circle cx="7" cy="7" r="7" fill="var(--red)"/><path d="M4.5 3.5 L6 5 L5.2 6 Q6 8 8 8.8 L9 8 L10.5 9.5 L9.5 10.5 Q5 10 3.5 4.5 Z" fill="#fff"/></svg>
          123-456-7890
        </li>
        <li>
          <svg viewBox="0 0 14 14"><rect x="3.5" y="1" width="7" height="12" rx="1.5" fill="var(--red)"/><rect x="5" y="2.5" width="4" height="6" fill="#fff"/></svg>
          456-085-4321
        </li>
        <li>
          <svg viewBox="0 0 14 14"><rect x="1" y="3" width="12" height="8" rx="1" fill="var(--red)"/><path d="M1.5 3.5 L7 7.5 L12.5 3.5" fill="none" stroke="#fff" stroke-width="1.2"/></svg>
          info@rbtolvane.com
        </li>
        <li>
          <svg viewBox="0 0 14 14"><circle cx="7" cy="7" r="6" fill="var(--red)"/><path d="M1 7 H13 M7 1 V13 M3 3.5 Q7 6 11 3.5 M3 10.5 Q7 8 11 10.5" fill="none" stroke="#fff" stroke-width="0.9"/></svg>
          www.rbtolvane.com
        </li>
      </ul>
    </div>
  </section>

</main>
</body>
</html>
```